BOLD & MINIMALIST DESIGN NEEDED

We want a very bold but minimalistic business card design that is impactful and utilizes both sides of the business card. Our current logo is included for your use.

We want bold fonts and good use of negative space. We don't want the logo to overpower the design.

Target Market(s)

Professionals who are building new commercial buildings.

Industry/Entity Type

Construction

Contact Information for Business Card

Name, Title, email, office phone, cell phone, website

Font styles to use
Serif
Sans Serif

Requirements
Must have
• Bold design!

```html
<!DOCTYPE html>
<html lang="en">
<head>
<meta charset="utf-8">
<title>Ridgeline Design + Build — Business Card</title>
<link href="https://fonts.googleapis.com/css2?family=Roboto:wght@400;700;900&display=swap" rel="stylesheet">
<style>
  :root {
    --stage: #2e2e2e;
    --card-dark: #111111;
    --card-dark-mark: #262626;
    --card-light: #ffffff;
    --ink: #161616;
    --ink-soft: #3a3a3a;
    --rule: #4a4a4a;
    --accent: #8dc63f;
  }
  * { box-sizing: border-box; margin: 0; padding: 0; }
  html, body {
    width: 1200px; height: 694px; overflow: hidden;
    background: var(--stage);
    font-family: "Roboto", Arial, sans-serif;
  }
  .canvas { position: relative; width: 1200px; height: 694px; }

  .card {
    position: absolute; top: 192px;
    width: 540px; height: 309px;
    border-radius: 22px; overflow: hidden;
  }

  /* Front side */
  .card-front { left: 40px; background: var(--card-dark); }
  .front-brand {
    position: absolute; inset: 0;
    display: flex; align-items: center; justify-content: center; gap: 14px;
    color: var(--card-dark-mark);
  }
  .front-brand .brand-square { width: 38px; height: 38px; background: var(--card-dark-mark); }
  .front-brand .brand-name { font-weight: 900; font-size: 34px; letter-spacing: 1px; text-transform: uppercase; }

  /* Back side */
  .card-back { left: 620px; background: var(--card-light); }
  .back-brand {
    position: absolute; top: 40px; right: 40px;
    display: flex; align-items: center; gap: 10px;
    color: var(--ink);
  }
  .back-brand .brand-square { width: 22px; height: 22px; background: var(--ink); }
  .back-brand .brand-name { font-weight: 900; font-size: 21px; text-transform: uppercase; letter-spacing: 0.5px; }

  .divider {
    position: absolute; left: 40px; right: 40px; top: 112px;
    height: 1px; background: var(--rule);
  }

  .person { position: absolute; left: 40px; top: 126px; }
  .person-name { color: var(--accent); font-weight: 700; font-size: 24px; line-height: 1.1; }
  .person-title { color: var(--ink-soft); font-size: 14px; margin-top: 4px; }

  .contacts { position: absolute; left: 40px; top: 190px; list-style: none; }
  .contacts li {
    display: flex; align-items: center; gap: 10px;
    font-size: 15px; color: var(--ink); line-height: 21px;
  }
  .contacts svg { width: 14px; height: 14px; fill: var(--ink); flex: none; }

  .address {
    position: absolute; right: 40px; top: 150px;
    text-align: right; font-size: 13px; line-height: 19px; color: var(--ink-soft);
  }

  .bands { position: absolute; left: 0; bottom: 0; width: 540px; height: 309px; }
  .website {
    position: absolute; right: 34px; bottom: 14px;
    color: var(--card-light); font-size: 13px; letter-spacing: 0.3px;
  }
</style>
</head>
<body>
<main class="canvas">

  <section class="card card-front" aria-label="Card front">
    <div class="front-brand">
      <span class="brand-square"></span>
      <span class="brand-name">Ridgeline Design + Build</span>
    </div>
  </section>

  <section class="card card-back" aria-label="Card back">
    <svg class="bands" viewBox="0 0 540 309" aria-hidden="true">
      <path d="M0 286 L322 286 C332 286 336 276 342 266 L356 266 C348 282 342 296 326 296 L0 296 Z" fill="var(--accent)"/>
      <path d="M0 299 L328 299 C344 299 350 282 358 270 C364 262 370 258 384 258 L540 258 L540 309 L0 309 Z" fill="var(--ink)"/>
    </svg>

    <div class="back-brand">
      <span class="brand-square"></span>
      <span class="brand-name">Ridgeline Design + Build</span>
    </div>

    <div class="divider"></div>

    <div class="person">
      <p class="person-name">Daniel Brooks</p>
      <p class="person-title">Owner</p>
    </div>

    <ul class="contacts">
      <li>
        <svg viewBox="0 0 16 16"><rect x="4" y="1" width="8" height="14" rx="1.5"/><rect x="5.5" y="3" width="5" height="8" fill="#fff"/></svg>
        044-123 456 789
      </li>
      <li>
        <svg viewBox="0 0 16 16"><path d="M3 1 L6 1 L7 5 L5 6.5 C6 9 7 10 9.5 11 L11 9 L15 10 L15 13 C15 14 14 15 13 15 C6.5 15 1 9.5 1 3 C1 2 2 1 3 1 Z"/></svg>
        044-123 456 789
      </li>
      <li>
        <svg viewBox="0 0 16 16"><path d="M1 3 H15 V13 H1 Z"/><path d="M1.5 3.5 L8 9 L14.5 3.5" fill="none" stroke="#fff" stroke-width="1.3"/></svg>
        info@webname.com
      </li>
    </ul>

    <p class="address">Address line goes here<br>45452, Country name</p>

    <p class="website">www.website.com</p>
  </section>

</main>
</body>
</html>
```